Non-profit organization needs newsletter

We are a non-profit organization that conducts medical missions overseas. We recently returned from a mission to Guangaje and Latacunga, Ecuador and need a newsletter describing our work to our supporters. We have a logo and would like the design to include the blue, green and white of the logo as well. The final design should be professional and communicate the culture of Ecuador using the photos of the people we helped and their corresponding stories
Updates

Reason: I NEED SOME SMALL CHANGES TO SOME DESIGN.

Target Market(s)

Prospective donors to our organization

Industry/Entity Type

Non Profit

Font styles to use
Sans Serif

Colors
9bcb3c
0456a4

Requirements
Must have
• 2 page newsletter, logo must be on the front page. Front page must feature pictures of the village of Guangaje and the text description. Front page must have the words GLOBAL VOLUNTEERISM COMPASSION ALTRUISM across the top of the page. Bottom of front page must have text that thanks donors for their support. Back page must have website address along the bottom. New hospital picture and text must be on back page. Pictures of patients and the corresponding text should be on the bottom of front page and also on the back page. Color theme is same colors in logo
Nice to have
• Pictures of random people can be untitled and just scattered throughout the newsletter.
Should not have
• Techno or modern design or non traditional font.

```html
<!DOCTYPE html>
<html lang="en">
<head>
<meta charset="utf-8">
<title>Cordillera Care Mission Newsletter</title>
<link href="https://fonts.googleapis.com/css2?family=Didact+Gothic&family=Roboto+Condensed:wght@400;700&display=swap" rel="stylesheet">
<style>
:root{
  --green:#9bcb3c;
  --blue:#0456a4;
  --tint:#f2f8e6;
  --backdrop:#74b8e6;
  --ink:#2a2a2a;
  --white:#ffffff;
}
*{box-sizing:border-box;margin:0;padding:0}
html,body{width:1170px;height:1200px;overflow:hidden}
body{background:var(--backdrop);font-family:"Didact Gothic",sans-serif;color:var(--ink);position:relative}
.page{position:absolute;top:98px;width:498px;height:1008px;background:var(--white)}
.page--front{left:74px}
.page--back{left:604px}
.abs{position:absolute}
.photo{position:absolute}
.frame{position:absolute;border:1.5px solid var(--white)}
.section-title{position:absolute;font-family:"Roboto Condensed",sans-serif;font-weight:700;color:var(--blue);font-size:11.5px;letter-spacing:.1px}
.rule{position:absolute;height:3px;background:var(--green)}
.body-text{position:absolute;font-size:10px;line-height:15.3px;letter-spacing:.25px}
.body-text p+p{margin-top:13px}

/* masthead */
.brand{left:26px;top:44px;width:150px;display:flex;align-items:center;gap:8px}
.brand__mark{flex:none;width:18px;height:18px;border-radius:50%;background:var(--blue)}
.brand__name{font-family:"Roboto Condensed",sans-serif;font-weight:700;color:var(--blue);font-size:15px;line-height:17px}
.date-box{left:393px;top:27px;width:83px;height:82px;background:var(--blue);color:var(--white);text-align:center;font-family:"Roboto Condensed",sans-serif;font-weight:700}
.date-box svg{margin-top:5px}
.date-box .d1{font-size:10px;line-height:13px}
.date-box .d2{font-size:15px;line-height:18px;margin-top:2px}
.headline{left:21px;top:133px;font-family:"Roboto Condensed",sans-serif;font-weight:700;color:var(--green);font-size:21.5px;letter-spacing:-.2px}

.intro{left:22px;top:380px;width:453px;height:294px;background:var(--tint)}
.intro__lead{position:absolute;left:8px;top:20px;width:430px;font-family:"Roboto Condensed",sans-serif;font-weight:700;color:var(--blue);font-size:11.5px;line-height:17px}

.thanks{left:99px;top:962px;width:377px;height:36px;background:var(--blue);color:var(--white);font-size:9.5px;line-height:13.5px;padding:4px 20px;letter-spacing:.3px}
.thanks-badge{left:44px;top:957px;width:42px;height:42px;border-radius:50%;background:var(--green);display:flex;align-items:center;justify-content:center}
.thanks-badge span{width:30px;height:30px;border-radius:50%;background:var(--blue);display:flex;align-items:center;justify-content:center}

/* back */
.people{left:22px;top:470px;width:452px;height:28px;background:var(--blue)}
.people__inner{left:28px;top:476px;width:446px;height:7px;background:var(--green)}
.hospital{left:22px;top:747px;width:452px;height:240px;overflow:hidden}
.brand-chip{left:29px;top:755px;width:80px;height:61px;background:var(--white);display:flex;align-items:center;justify-content:center;text-align:center;padding:6px}
.brand-chip .nm{font-family:"Roboto Condensed",sans-serif;font-weight:700;color:var(--blue);font-size:9px;line-height:11px}
.contact{color:var(--white);font-size:10.5px;letter-spacing:.4px}
.contact--web{left:285px;top:886px;color:var(--green)}
.contact--follow{left:276px;top:914px;font-family:"Roboto Condensed",sans-serif;font-weight:700;color:var(--green);letter-spacing:.6px}
.contact--name{left:276px;top:931px}
.icon-ring{position:absolute;width:28px;height:28px;border-radius:50%;border:3px solid var(--green);background:var(--blue);display:flex;align-items:center;justify-content:center}
.social{position:absolute;top:951px;width:26px;height:26px;border-radius:50%;background:var(--white)}
strong.hl{color:var(--blue);font-weight:700;font-family:"Roboto Condensed",sans-serif;letter-spacing:.5px}
</style>
</head>
<body>

<!-- FRONT PAGE -->
<section class="page page--front">
  <div class="abs brand">
    <span class="brand__mark"></span>
    <span class="brand__name">Cordillera Care Mission</span>
  </div>

  <div class="abs date-box">
    <svg width="20" height="20" viewBox="0 0 20 20"><circle cx="10" cy="10" r="7" fill="none" stroke="#9bcb3c" stroke-width="2.4"/><path d="M10 6v4l3 2" fill="none" stroke="#9bcb3c" stroke-width="2"/></svg>
    <div class="d1">14th<br>November ,</div>
    <div class="d2">2017</div>
  </div>

  <div class="rule" style="left:26px;top:123px;width:449px;height:1.5px;background:#dfeccb"></div>
  <h1 class="abs headline">GLOBAL VOLUNTEERISM COMPASSION ALTRUISM</h1>

  <div class="photo" role="img" aria-label="Team of smiling volunteer doctors and nurses in white coats" style="left:22px;top:167px;width:453px;height:213px;background:linear-gradient(180deg,#8ec6e4 0%,#dce9f1 55%,#eef3f6 100%)"></div>
  <div class="abs" style="left:53px;top:298px;width:96px;height:82px;background:var(--green)"></div>
  <div class="photo" role="img" aria-label="Hillside houses of the village of Guangaje" style="left:57px;top:303px;width:92px;height:77px;background:linear-gradient(180deg,#a9c7dd 0%,#9c9a88 60%,#7d7464 100%)"></div>
  <div class="abs" style="left:147px;top:268px;width:182px;height:112px;background:var(--blue)"></div>
  <div class="photo" role="img" aria-label="Guangaje market square with church bell tower" style="left:155px;top:276px;width:167px;height:104px;background:linear-gradient(180deg,#9cc4e6 0%,#c9d8e3 45%,#9b6a5a 75%,#4b3f3a 100%)"></div>
  <div class="abs" style="left:329px;top:298px;width:108px;height:82px;background:var(--green)"></div>
  <div class="photo" role="img" aria-label="Village community information centre building" style="left:329px;top:303px;width:103px;height:77px;background:linear-gradient(180deg,#d6d3cc 0%,#eceae6 50%,#f5f5f3 100%)"></div>

  <div class="abs intro">
    <div class="intro__lead">THE CORDILLERA CARE MISSION TEAM PARTNERS AGAIN WITH KINDRED RELIEF TO PROVIDE SPECIALTY SURGICAL CARE TO THE INDIGENT MESTIZOS PEOPLE OF THE SMALL VILLAGE OF GUANGAJE, ECUADOR.</div>
    <div class="rule" style="left:8px;top:73px;width:431px"></div>
    <div class="body-text" style="left:8px;top:84px;width:430px">
      <p>The town of Guangaje was established in 1861. The population, being 95% indigenous Indians, used to work for Spanish estates until they themselves became landowners. It presently has a population of just over 7000 people, but lacks basic services like potable water, sewage systems, advanced educational programs, and in some areas, electricity.</p>
      <p>Guangaje does have a small Health Center and a church, St. John the Baptist. Kindred Relief provides medical services to people in remote villages like Guangaje and then partners with volunteer organizations like CCM to provide specialty surgical care. The CCM Team travelled to Guangaje to conduct a surgical clinic. We then assisted Kindred Relief in transporting the villagers in need of surgery to the Hospital Provincial del Valle in Latacunga, about 2 hours away, where the Team performed the surgery.</p>
    </div>
  </div>

  <h2 class="section-title" style="left:30px;top:687px">SEE SOME POSITIVE RESULTS WORKS ON TREATMENT HERE</h2>
  <div class="rule" style="left:30px;top:706px;width:431px"></div>

  <div class="abs" style="left:22px;top:718px;width:135px;height:232px;background:var(--green)"></div>
  <div class="photo" role="img" aria-label="Young boy in a surgical cap before his procedure" style="left:27px;top:726px;width:157px;height:96px;background:linear-gradient(160deg,#4d6fb5 0%,#8fa3c9 45%,#c79a7e 100%)"></div>
  <div class="frame" style="left:41px;top:735px;width:133px;height:78px"></div>
  <div class="photo" role="img" aria-label="Little girl in a knitted hat with a facial rash" style="left:31px;top:832px;width:156px;height:106px;background:linear-gradient(160deg,#d44c7b 0%,#b98f7a 45%,#59b3c4 100%)"></div>
  <div class="frame" style="left:44px;top:846px;width:131px;height:78px"></div>

  <div class="body-text" style="left:200px;top:724px;width:276px">This is Mateo Ruiz, a 1-year old who lives with his Mom in Guangaje. Mateo presented to us with an enlarging mass behind his left ear that was causing him pain and concern to his Mom. The CCM Team successfully removed the mass and a full recovery is anticipated.</div>
  <div class="body-text" style="left:200px;top:830px;width:276px">This is 5 year-old Lucia Pazmino from Guangaje who has suffered from a facial rash for several months. Many local doctors have seen her but none have been able to successfully treat her. The CCM Team saw her and outlined a treatment plan of a topical cream and oral medication which will finally resolve the rash.</div>

  <div class="abs thanks-badge"><span><svg width="18" height="12" viewBox="0 0 18 12"><path d="M1 6l4-4h3l2 2 3-2h4M3 6l5 5 3-2 2 1 4-4" fill="none" stroke="#f5b942" stroke-width="1.8" stroke-linejoin="round"/></svg></span></div>
  <div class="abs thanks">Thank you to all our Friends and Family whose contributions made this mission possible.</div>
</section>

<!-- BACK PAGE -->
<section class="page page--back">
  <h2 class="section-title" style="left:21px;top:33px">MORE TREATMENT RESULTS</h2>
  <div class="rule" style="left:21px;top:52px;width:451px"></div>

  <div class="abs" style="left:22px;top:66px;width:134px;height:348px;background:var(--green)"></div>
  <div class="abs" style="left:187px;top:184px;width:299px;height:97px;background:var(--tint)"></div>

  <div class="photo" role="img" aria-label="Patient lying on an operating table with a scalp mass" style="left:28px;top:74px;width:156px;height:97px;background:linear-gradient(160deg,#7a8fae 0%,#3c5a92 50%,#27447f 100%)"></div>
  <div class="frame" style="left:41px;top:83px;width:131px;height:78px"></div>
  <div class="photo" role="img" aria-label="Older man in a surgical cap with a tumor above his eye" style="left:30px;top:182px;width:157px;height:104px;background:linear-gradient(160deg,#3d9fbf 0%,#8e7260 50%,#5a4a44 100%)"></div>
  <div class="frame" style="left:44px;top:195px;width:131px;height:78px"></div>
  <div class="photo" role="img" aria-label="Young girl with burn wounds receiving dressings" style="left:30px;top:299px;width:157px;height:105px;background:linear-gradient(90deg,#c9906e 0%,#6f8c96 48%,#9aa4ae 100%)"></div>
  <div class="abs" style="left:113px;top:299px;width:3px;height:105px;background:var(--blue)"></div>
  <div class="frame" style="left:44px;top:313px;width:131px;height:78px"></div>

  <div class="body-text" style="left:199px;top:72px;width:280px">45-year old Luis Cando lives in a remote village outside of Guangaje. He travelled 4 hours to have the CCM Team evaluate a large scalp mass causing him significant pain. We were able to successfully remove the mass, allowing Luis to return to work on his farm pain free.</div>
  <div class="body-text" style="left:199px;top:197px;width:280px">54 year-old Pedro Chusin from Guangaje presented to the CCM Team suffering for many years with a tumor above his right eye, which impeded his vision and caused him pain. We were able to successfully remove the mass and expect Pedro to recover fully.</div>
  <div class="body-text" style="left:199px;top:304px;width:280px">The CCM Team had the opportunity to help treat Rosa Quishpe, a 4-year old girl who suffered burns to half her body when her family was burning garbage to stay warm. We instructed the hospital staff on burn care and provided specialized dressings donated to us by our supporters back home.</div>

  <h2 class="section-title" style="left:21px;top:435px">RANDOM PEOPLE</h2>
  <div class="rule" style="left:21px;top:453px;width:451px"></div>
  <div class="abs people"></div>
  <div class="abs people__inner"></div>
  <div class="photo" role="img" aria-label="Elderly man in a felt hat and red poncho" style="left:27px;top:483px;width:105px;height:120px;background:linear-gradient(180deg,#e7ecef 0%,#a1757a 55%,#7b2d38 100%)"></div>
  <div class="photo" role="img" aria-label="Villagers seated in a clinic waiting room" style="left:139px;top:483px;width:105px;height:120px;background:linear-gradient(180deg,#7fb0c9 0%,#6b6e72 50%,#4c4a4e 100%)"></div>
  <div class="photo" role="img" aria-label="Man in a red sweater" style="left:251px;top:483px;width:105px;height:120px;background:linear-gradient(180deg,#2c3b38 0%,#b0383e 55%,#d8474e 100%)"></div>
  <div class="photo" role="img" aria-label="Man in a cap and striped poncho" style="left:364px;top:483px;width:105px;height:120px;background:linear-gradient(180deg,#4f8ac4 0%,#c99a87 40%,#c94c5c 100%)"></div>

  <h2 class="section-title" style="left:22px;top:637px">HOSPITAL PROVINCIAL DEL VALLE</h2>
  <div class="rule" style="left:22px;top:655px;width:451px"></div>
  <div class="body-text" style="left:23px;top:664px;width:452px">This is the new Hospital Provincial del Valle in Latacunga, planned to be open in the next several months. It is adjacent to the old hospital and built to better serve the nearly 100K inhabitants of the Cotopaxi providence. <strong class="hl">THE CCM TEAM</strong> looks forward to working there during our mission next year.</div>

  <div class="hospital" role="img" aria-label="Exterior of the new provincial hospital building in Latacunga" style="position:absolute;background:linear-gradient(110deg,#5b8fc7 0%,#9db6cf 35%,#c2c6cc 55%,#b23b3e 75%,#c64447 100%)"></div>
  <svg class="abs" style="left:22px;top:747px" width="452" height="240" viewBox="0 0 452 240">
    <polygon points="272,99 452,99 452,240 190,240" fill="#0456a4"/>
    <line x1="272" y1="99" x2="190" y2="240" stroke="#ffffff" stroke-width="3"/>
  </svg>
  <div class="abs brand-chip">
    <div class="nm">Cordillera Care Mission</div>
  </div>

  <div class="icon-ring" style="left:249px;top:878px"><svg width="12" height="12" viewBox="0 0 12 12"><circle cx="6" cy="6" r="5" fill="none" stroke="#9bcb3c" stroke-width="1.5"/><path d="M1 6h10M6 1c-3 3-3 7 0 10M6 1c3 3 3 7 0 10" fill="none" stroke="#9bcb3c" stroke-width="1"/></svg></div>
  <div class="abs contact contact--web">www.cordilleracare.org</div>
  <div class="icon-ring" style="left:236px;top:913px"><svg width="14" height="12" viewBox="0 0 14 12"><circle cx="5" cy="4" r="2.5" fill="#9bcb3c"/><circle cx="10" cy="4.5" r="2" fill="#9bcb3c"/><path d="M0.5 11.5c0-3 2-4.5 4.5-4.5s4.5 1.5 4.5 4.5zM10 7.5c2 0 3.5 1.2 3.5 4h-3" fill="#9bcb3c"/></svg></div>
  <div class="abs contact contact--follow">PLEASE FOLLOW US ON</div>
  <div class="abs contact contact--name">Cordillera Care Mission</div>
  <div class="social" style="left:276px"></div>
  <div class="social" style="left:309px"></div>
</section>

</body>
</html>
```